To design a brand identity that is simple and creative with 'Corvane' as the brand name, I like modern simple fonts like helvetica neue, I want to print both sides of the card, I am open to dark front and white back, but the design needs to transfer well to letter heads and email signatures, I am looking for sophisticated and elegant, but open minded about clever and off the wall, I do not do 'boring' Corvane Ventures is the mother company for a small group, specialising in Management & consulting, Software development and construction, we have a high level of integrity, we are transparent and accountable for what we do. my images are provided as a guide only, Im not expecting them to be just copied, Im looking for a creator and passionate thinker, who will put life into their work.

Target Market(s)

usually business minded people who are looking for something different in me, such as leadership, confidence and focus with thinking that is per haps a little outside the box..

Industry/Entity Type

Construction

Requirements
Must have
• clean, minmalistic
Nice to have
• custom logo
Should not have
• boring, traditional

```html
<!DOCTYPE html>
<html lang="en">
<head>
<meta charset="utf-8">
<title>Corvane — Business Card</title>
<link rel="stylesheet" href="https://fonts.googleapis.com/css2?family=Work+Sans:wght@300;400&display=swap">
<style>
  :root {
    --stage: #2f2b29;
    --card-light: #ffffff;
    --card-light-edge: #ececee;
    --card-dark-core: #575350;
    --card-dark-edge: #262525;
    --accent: #e8603c;
    --accent-strong: #e23b1f;
    --ink: #1f1f1f;
    --ink-soft: #666666;
    --tagline: #7a7a7a;
    --paper-text: #ffffff;
    --dot: #d8342c;
  }
  * { box-sizing: border-box; margin: 0; padding: 0; }
  html, body {
    width: 1000px; height: 1200px; overflow: hidden;
    background: var(--stage);
    font-family: "Work Sans", "Helvetica Neue", Arial, sans-serif;
  }
  .canvas { position: relative; width: 1000px; height: 1200px; }

  .card { position: absolute; width: 740px; height: 456px; overflow: hidden; }

  /* front */
  .card--front {
    left: 135px; top: 75px;
    background: linear-gradient(160deg, var(--card-light) 40%, var(--card-light-edge));
  }
  .brand {
    position: absolute; left: 48px; top: 204px;
    display: flex; align-items: center; gap: 20px;
  }
  .brand__dot { width: 42px; height: 42px; border-radius: 50%; background: var(--accent); }
  .brand__name {
    font-weight: 300; font-size: 52px; line-height: 1; color: var(--accent);
    letter-spacing: 0.3px;
  }
  .brand__tagline {
    position: absolute; right: 425px; top: 268px;
    font-weight: 300; font-size: 14px; letter-spacing: 0.6px; color: var(--tagline);
  }
  .services-vertical {
    position: absolute; left: 372px; top: 228px;
    width: 345px; transform: translate(-50%, -50%) rotate(-90deg);
    text-align: center; font-size: 15px; letter-spacing: 1.2px; color: var(--ink);
    white-space: nowrap;
  }
  .sep { color: var(--dot); padding: 0 4px; }

  .contact { position: absolute; left: 454px; top: 136px; color: var(--ink); }
  .contact__name { font-size: 26px; color: var(--accent-strong); line-height: 1; }
  .contact__role { font-size: 16px; color: var(--ink-soft); margin-top: 6px; }
  .contact__list { list-style: none; font-size: 18.5px; margin-top: 8px; }
  .contact__list li { line-height: 28px; }
  .contact__list li.gap { margin-top: 13px; }
  .label { color: var(--accent); margin-right: 4px; }

  /* back */
  .card--back {
    left: 117px; top: 652px;
    background: radial-gradient(ellipse at 50% 35%, var(--card-dark-core), var(--card-dark-edge) 75%);
    display: flex; flex-direction: column; align-items: center; justify-content: center;
  }
  .brand--back { display: flex; align-items: center; gap: 26px; margin-top: 8px; }
  .brand--back .brand__dot { width: 72px; height: 72px; }
  .brand--back .brand__name { font-size: 94px; color: var(--paper-text); }
  .services-line {
    margin-top: 22px; font-size: 16px; letter-spacing: 1.6px; color: var(--paper-text);
  }
</style>
</head>
<body>
<main class="canvas">
  <section class="card card--front" aria-label="Card front">
    <div class="brand">
      <span class="brand__dot"></span>
      <span class="brand__name">corvane.</span>
    </div>
    <p class="brand__tagline">built with intent</p>
    <p class="services-vertical">management<span class="sep">•</span>software<span class="sep">•</span>construction</p>
    <div class="contact">
      <p class="contact__name">Mara Quill</p>
      <p class="contact__role">client ambassador</p>
      <ul class="contact__list">
        <li><span class="label">c.</span> +61 0400 118 274</li>
        <li><span class="label">e.</span> info@corvane.com.au</li>
        <li class="gap"><span class="label">a.</span> po box 481 perth 6010</li>
        <li><span class="label">w.</span> www.corvane.com.au</li>
      </ul>
    </div>
  </section>

  <section class="card card--back" aria-label="Card back">
    <div class="brand--back">
      <span class="brand__dot"></span>
      <span class="brand__name">corvane.</span>
    </div>
    <p class="services-line">management <span class="sep">•</span> software <span class="sep">•</span> construction</p>
  </section>
</main>
</body>
</html>
```